Website for new crypto research organization

See brief (attached). This is a pretty basic website with only a handful of pages + ability to collect email addresses.

```html
<!DOCTYPE html>
<html lang="en">
<head>
<meta charset="utf-8">
<title>Seaglass Ledger — Crypto Research</title>
<link href="https://fonts.googleapis.com/css2?family=Outfit:wght@400;500;600;700&family=Poppins:wght@400;500&display=swap" rel="stylesheet">
<style>
:root{
  --teal:#149a8c;
  --teal-dark:#0f8175;
  --ink:#111111;
  --text:#555555;
  --muted:#666666;
  --page:#f8f8f8;
  --white:#ffffff;
  --line:#dddddd;
}
*{margin:0;padding:0;box-sizing:border-box}
html,body{width:1200px;height:2731px;overflow:hidden}
body{position:relative;background:var(--page);font-family:"Outfit",sans-serif;color:var(--ink)}
a{color:inherit;text-decoration:none}
.abs{position:absolute}

/* header */
.site-header{position:absolute;left:0;top:0;width:1200px;height:111px;background:var(--white)}
.brand{position:absolute;left:117px;top:36px;display:flex;align-items:center;gap:10px;font-family:"Outfit",sans-serif;font-weight:600;font-size:20px;color:var(--teal)}
.brand-mark{width:22px;height:22px;background:var(--teal)}
.main-nav{position:absolute;top:44px;left:0;width:1200px;height:24px;font-size:16px;color:#222}
.main-nav a{position:absolute;transform:translateX(-50%);white-space:nowrap}
.main-nav a.active{color:var(--teal)}
.login svg{vertical-align:-2px;margin-right:3px}

/* hero */
.hero{position:absolute;left:0;top:105px;width:1200px;height:590px}
.hero-art{position:absolute;inset:0;background:linear-gradient(100deg,#8a8a88 0%,#9b9a97 35%,#6b4a35 58%,#5d8fa8 75%,#c8a24a 88%,#7aa0c8 100%)}
.hero-edge{position:absolute;left:0;bottom:0;width:1200px;height:30px}
.hero-frame-back{position:absolute;left:33px;top:93px;width:518px;height:351px;border:1.5px solid #222}
.hero-panel{position:absolute;left:66px;top:128px;width:515px;height:350px;background:rgba(245,245,245,.78)}
.hero-frame-front{position:absolute;left:90px;top:157px;width:518px;height:351px;border:1.5px solid #222}
.hero-title{position:absolute;left:117px;top:172px;font-family:"Outfit",sans-serif;font-weight:600;font-size:70px;line-height:80px;color:#000;letter-spacing:-.5px}
.hero-text{position:absolute;left:117px;top:335px;width:430px;font-family:"Poppins",sans-serif;font-size:15px;line-height:30px;color:#111}
.slider-dots{position:absolute;left:1022px;top:497px;display:flex;gap:7px}
.slider-dots span{width:12px;height:12px;border:2px solid var(--white);border-radius:50%}
.slider-dots span.on{background:var(--white)}

/* section headings */
.section-title{position:absolute;left:0;width:1200px;text-align:center;font-weight:700;font-size:46px;line-height:56px}
.section-lead{position:absolute;left:300px;width:600px;text-align:center;font-family:"Poppins",sans-serif;font-size:14.5px;line-height:26px;color:var(--text)}
.rule{position:absolute;left:544px;width:111px;height:4px;background:var(--teal)}

/* research features */
.feature{position:absolute;top:953px;width:307px;text-align:center}
.feature-icon{width:136px;height:136px;margin:0 auto;border-radius:50%;background:var(--teal);display:flex;align-items:center;justify-content:center;box-shadow:0 3px 6px rgba(0,0,0,.15)}
.feature h3{margin-top:20px;font-weight:600;font-size:18px;line-height:24px;color:#111}
.feature p{margin-top:8px;font-family:"Poppins",sans-serif;font-size:13.5px;line-height:26px;color:var(--text)}
.btn-reports{position:absolute;left:453px;top:1265px;width:295px;height:57px;background:var(--teal);color:var(--white);font-weight:500;font-size:16px;display:flex;align-items:center;justify-content:center;box-shadow:0 3px 6px rgba(0,0,0,.2)}

/* recent research */
.recent{position:absolute;left:0;top:1397px;width:1200px;height:640px;background:var(--teal)}
.recent .section-title,.recent .section-lead{color:var(--white)}
.recent .rule{background:var(--white)}
.card{position:absolute;top:218px;width:317px;height:352px;background:var(--white);border-radius:5px;padding:25px 16px 0 16px}
.card h3{font-weight:600;font-size:19px;line-height:28px;color:#111}
.card time{display:block;margin-top:5px;font-family:"Poppins",sans-serif;font-size:14px;color:#333}
.card p{margin-top:24px;padding-left:1px;font-family:"Poppins",sans-serif;font-size:13.3px;line-height:27.5px;color:var(--text)}
.card .more{position:absolute;left:13px;top:285px;font-weight:500;font-size:15px;color:var(--teal);border-bottom:1px solid var(--teal)}

/* newsletter */
.email-field{position:absolute;left:218px;top:2301px;width:514px;height:68px;border-radius:34px;background:var(--white);box-shadow:0 2px 8px rgba(0,0,0,.12);padding-left:29px;display:flex;align-items:center;font-size:15px;color:#222}
.btn-subscribe{position:absolute;left:750px;top:2301px;width:231px;height:68px;border-radius:34px;background:var(--teal);color:var(--white);font-weight:600;font-size:20px;display:flex;align-items:center;justify-content:center}

/* footer */
.footer-line{position:absolute;left:0;top:2457px;width:1200px;height:1px;background:var(--line)}
.footer-nav{position:absolute;left:0;top:2537px;width:1200px;height:26px;font-size:18.5px;color:#222}
.footer-nav a{position:absolute;transform:translateX(-50%);white-space:nowrap}
.social{position:absolute;top:2586px;width:44px;height:44px;border:1px solid #ccc;border-radius:50%;background:var(--white)}
.social::after{content:"";position:absolute;left:16px;top:16px;width:12px;height:12px;border-radius:50%;background:#333}
.copyright{position:absolute;left:0;top:2659px;width:1200px;text-align:center;font-size:15px;color:#333}
</style>
</head>
<body>

<header class="site-header">
  <a class="brand" href="#"><span class="brand-mark"></span>Seaglass Ledger</a>
  <nav class="main-nav">
    <a class="active" href="#" style="left:493px">Home</a>
    <a href="#" style="left:586px">About Us</a>
    <a href="#" style="left:690px">Research</a>
    <a href="#" style="left:781px">News</a>
    <a href="#" style="left:867px">Careers</a>
    <a href="#" style="left:964px">Contact</a>
    <a class="login" href="#" style="left:1058px"><svg width="11" height="13" viewBox="0 0 11 13"><circle cx="5.5" cy="3.3" r="3.1" fill="#149a8c"/><path d="M0 13c0-4 2.3-5.8 5.5-5.8S11 9 11 13z" fill="#149a8c"/></svg>Login</a>
  </nav>
</header>

<section class="hero">
  <div class="hero-art" role="img" aria-label="Street-art photo: an elephant bursting through a graffiti brick wall with a red heart painted on it"></div>
  <svg class="hero-edge" viewBox="0 0 1200 30" preserveAspectRatio="none"><path d="M0 12 L40 18 L80 10 L120 20 L170 12 L220 19 L260 9 L310 17 L360 11 L410 20 L460 10 L510 18 L560 12 L610 21 L660 10 L710 18 L760 11 L810 20 L860 9 L910 17 L960 12 L1010 19 L1060 10 L1110 18 L1160 11 L1200 16 L1200 30 L0 30Z" fill="#f8f8f8"/></svg>
  <div class="hero-frame-back"></div>
  <div class="hero-panel"></div>
  <div class="hero-frame-front"></div>
  <h1 class="hero-title">Seaglass<br>Ledger</h1>
  <p class="hero-text">Lorem ipsum dolor sit amet, consectetur adipiscing elit, sed do eiusmod tempor incididunt ut labore et dolore magna aliqua. Ut enim ad minim veniam,</p>
  <div class="slider-dots"><span class="on"></span><span></span><span></span><span></span></div>
</section>

<h2 class="section-title" style="top:757px">Research</h2>
<p class="section-lead" style="top:823px">Lorem ipsum dolor sit amet, consectetur adipiscing elit, sed do eiusmod tempor incididunt ut labore et dolore magna aliqua.</p>
<div class="rule" style="top:899px"></div>

<div class="feature" style="left:114px">
  <div class="feature-icon">
    <svg width="80" height="80" viewBox="0 0 80 80" fill="none" stroke="#fff" stroke-width="2.5"><circle cx="40" cy="40" r="10"/><circle cx="40" cy="40" r="20"/><path d="M40 14v6M40 60v6M14 40h6M60 40h6M22 22l4 4M54 54l4 4M58 22l-4 4M22 58l4-4"/><path d="M12 52a30 30 0 0 1 48-36M68 28a30 30 0 0 1-48 36" stroke-dasharray="4 4"/></svg>
  </div>
  <h3>Technical Evaluation</h3>
  <p>Lorem ipsum dolor sit amet, adipiscing elit, sed do eiusmod tempor incididunt ut labore et dolore magna aliqua.</p>
</div>
<div class="feature" style="left:448px">
  <div class="feature-icon">
    <svg width="80" height="80" viewBox="0 0 80 80" fill="none" stroke="#fff" stroke-width="2.5"><circle cx="40" cy="30" r="26" stroke-dasharray="3 4"/><circle cx="28" cy="24" r="5"/><circle cx="40" cy="22" r="5"/><circle cx="52" cy="24" r="5"/><path d="M20 42c0-6 4-10 8-10s8 4 8 10M32 40c0-6 4-10 8-10s8 4 8 10M44 42c0-6 4-10 8-10s8 4 8 10"/><path d="M10 52h8v18h-8zM18 56h16l14 4c4 1 4 6 0 6H32M18 66l16 4 30-12c3-1 2-6-2-5l-14 5"/></svg>
  </div>
  <h3>Community Engagement</h3>
  <p>Lorem ipsum dolor sit amet, adipiscing elit, sed do eiusmod tempor incididunt ut labore et dolore magna aliqua.</p>
</div>
<div class="feature" style="left:782px">
  <div class="feature-icon">
    <svg width="80" height="80" viewBox="0 0 80 80" fill="none" stroke="#fff" stroke-width="2.5"><rect x="8" y="14" width="50" height="40"/><path d="M14 22h14M14 28h14M14 34h10"/><path d="M14 50v-6M20 50v-9M26 50v-5M32 50v-12"/><path d="M34 32l8-8 6 4 12-12"/><circle cx="64" cy="14" r="4"/><circle cx="54" cy="56" r="14"/><circle cx="54" cy="56" r="8"/><circle cx="54" cy="56" r="3"/></svg>
  </div>
  <h3>On-chain data analysis</h3>
  <p>Lorem ipsum dolor sit amet, adipiscing elit, sed do eiusmod tempor incididunt ut labore et dolore magna aliqua.</p>
</div>

<a class="btn-reports" href="#">RECENT RESEARCH REPORTS</a>

<section class="recent">
  <h2 class="section-title" style="top:59px">Recent Research</h2>
  <p class="section-lead" style="top:117px">Lorem ipsum dolor sit amet, consectetur adipiscing elit, sed do eiusmod tempor incididunt ut labore et dolore magna aliqua.</p>
  <div class="rule" style="top:182px"></div>

  <article class="card" style="left:111px">
    <h3>Lorem ipsum dolor sit amet,</h3>
    <time>25-01-2022</time>
    <p>Lorem ipsum dolor sit amet, consectetur adipiscing elit, sed do eiusmodincididunt ut labore et dolore magna aliqua. Ut enim ad minim veniam, Lorem ipsum dolor sit amet, consectetur adipiscing elit, sed do eiusmod tempor incididunt</p>
    <a class="more" href="#">Read More</a>
  </article>
  <article class="card" style="left:441px">
    <h3>Lorem ipsum dolor sit amet,</h3>
    <time>25-01-2022</time>
    <p>Lorem ipsum dolor sit amet, consectetur adipiscing elit, sed do eiusmodincididunt ut labore et dolore magna aliqua. Ut enim ad minim veniam, Lorem ipsum dolor sit amet, consectetur adipiscing elit, sed do eiusmod tempor incididunt</p>
    <a class="more" href="#">Read More</a>
  </article>
  <article class="card" style="left:772px">
    <h3>Lorem ipsum dolor sit amet,</h3>
    <time>25-01-2022</time>
    <p>Lorem ipsum dolor sit amet, consectetur adipiscing elit, sed do eiusmodincididunt ut labore et dolore magna aliqua. Ut enim ad minim veniam, Lorem ipsum dolor sit amet, consectetur adipiscing elit, sed do eiusmod tempor incididunt</p>
    <a class="more" href="#">Read More</a>
  </article>
</section>

<h2 class="section-title" style="top:2121px">Newsletter</h2>
<p class="section-lead" style="top:2187px">Lorem ipsum dolor sit amet, consectetur adipiscing elit, sed do eiusmod tempor incididunt ut labore et dolore magna aliqua.</p>
<div class="rule" style="top:2261px"></div>
<div class="email-field">Please enter your email</div>
<a class="btn-subscribe" href="#">SUBSCRIBE NOW</a>

<div class="footer-line"></div>
<nav class="footer-nav">
  <a href="#" style="left:320px">Home</a>
  <a href="#" style="left:429px">About Us</a>
  <a href="#" style="left:550px">Research</a>
  <a href="#" style="left:656px">News</a>
  <a href="#" style="left:758px">Careers</a>
  <a href="#" style="left:869px">Contact</a>
</nav>
<a class="social" href="#" style="left:551px" aria-label="Social profile one"></a>
<a class="social" href="#" style="left:604px" aria-label="Social profile two"></a>
<p class="copyright">© 2022 All Rights Reserved</p>

</body>
</html>
```